Tidewell Homecare

I am looking to have a website designed for a housekeeping company that looks similar to this one. https://marloweshomecare.example/

I need 5 websites designed but will start with this one to see how I like it.

Industry/Entity Type

House Cleaning

Coding

Coded - Design and coding required

Number of Pages Required

5+ page

Font styles to use
Serif
Script

Colors
ffffff
fdf9cf
fbf289
fbee3f
d6edf3
86cae7
33a6d7
edf1f8
cedeed

```html
<!DOCTYPE html>
<html lang="en">
<head>
<meta charset="utf-8">
<title>Tidewell Homecare</title>
<link href="https://fonts.googleapis.com/css2?family=Roboto+Condensed:ital,wght@0,300;0,400;0,700;1,700&display=swap" rel="stylesheet">
<style>
:root{
  --white:#ffffff;
  --cream:#fdf9cf;
  --yellow-soft:#fbf289;
  --yellow:#fbee3f;
  --sky-pale:#d6edf3;
  --sky:#86cae7;
  --blue:#33a6d7;
  --blue-deep:#2b8fc9;
  --mist:#edf1f8;
  --steel:#cedeed;
  --ink:#1d1d1d;
  --text:#555a60;
}
*{box-sizing:border-box;margin:0;padding:0}
html,body{width:1200px;height:3502px;overflow:hidden}
body{font-family:"Roboto Condensed",sans-serif;color:var(--ink);background:var(--white);position:relative}
.abs{position:absolute}
.btn{position:absolute;background:var(--yellow);color:var(--blue);font-weight:700;font-size:17px;text-transform:uppercase;display:flex;align-items:center;justify-content:center;border-radius:24px 24px 0 24px;text-decoration:none}

/* header */
.top-rule{top:0;left:0;width:1200px;height:4px;background:var(--yellow)}
.header{top:4px;left:0;width:1200px;height:109px;background:var(--white)}
.brand{top:0;left:143px;width:204px;height:186px;border-radius:0 0 102px 102px;background:var(--white);display:flex;flex-direction:column;align-items:center;justify-content:center;padding-top:30px;z-index:3}
.brand-mark{width:28px;height:28px;border-radius:50%;background:var(--yellow);margin-bottom:10px}
.brand-name{font-size:22px;font-weight:700;color:var(--ink);text-align:center;line-height:1.1}
.phone{top:12px;left:630px;display:flex;align-items:center;gap:10px;font-size:27px;font-weight:700}
.nav{top:70px;left:416px;display:flex;font-size:16px;color:var(--ink)}
.nav span{position:absolute;white-space:nowrap}
.nav .active{color:var(--blue);border-bottom:3px solid var(--yellow);padding-bottom:5px}

/* hero */
.hero{top:113px;left:0;width:1200px;height:664px;background:linear-gradient(180deg,#5c5f63 0%,#8a8276 45%,#6a4e37 100%)}
.hero h1{position:absolute;top:230px;left:0;width:1200px;text-align:center;color:var(--white);font-size:58px;line-height:66px;font-weight:700;text-transform:uppercase;text-shadow:0 2px 6px rgba(0,0,0,.5)}
.hero p{position:absolute;top:386px;left:0;width:1200px;text-align:center;color:var(--white);font-size:19px;line-height:29px;text-shadow:0 1px 4px rgba(0,0,0,.6)}
.arrow{width:60px;height:60px;border-radius:50%;background:rgba(20,20,20,.85);display:flex;align-items:center;justify-content:center}
.dots{top:597px;left:553px;display:flex;gap:10px}
.dots i{width:11px;height:11px;border-radius:50%;background:var(--white);display:block}
.dots i.on{background:var(--yellow)}

/* about */
.about-photo{top:777px;left:0;width:600px;height:551px;background:linear-gradient(160deg,#e9e7e4 0%,#8f8a93 45%,#5b5b66 100%)}
.about{top:777px;left:600px;width:600px;height:551px;background:var(--blue)}
.about h2{position:absolute;top:82px;left:65px;font-size:56px;color:var(--white);font-weight:700}
.about p{position:absolute;top:171px;left:65px;width:420px;font-size:16px;line-height:29px;color:var(--white);font-weight:300}

/* services */
.service{top:1400px;width:440px;text-align:center}
.service h3{font-size:24px;font-weight:700;text-transform:uppercase;margin-top:52px}
.service p{font-size:15px;line-height:30px;color:var(--text);margin-top:28px;font-weight:300}

/* estimate */
.estimate{top:1870px;left:0;width:1200px;height:463px;background:var(--sky-pale)}
.estimate h2{position:absolute;top:85px;left:0;width:1200px;text-align:center;font-size:58px;font-weight:700}
.field{position:absolute;width:294px;height:47px;background:var(--white);border:1px solid var(--steel);font-size:14px;color:var(--text);display:flex;align-items:center;padding:0 20px;justify-content:space-between}
.submit{position:absolute;width:294px;height:46px;background:var(--yellow);color:var(--blue);font-weight:700;font-size:17px;display:flex;align-items:center;justify-content:center}

/* testimonial */
.testimonial{top:2333px;left:0;width:1200px;height:631px;background:linear-gradient(90deg,#4a4a4d 0%,#5a5756 45%,#b07a2a 70%,#d8a21c 100%)}
.quote{position:absolute;top:202px;left:140px;width:510px;text-align:center;color:var(--white);font-size:36px;line-height:43px;font-style:italic;font-weight:700}
.author{position:absolute;top:435px;left:140px;width:510px;text-align:center;color:var(--yellow);font-size:34px;font-style:italic;font-weight:700}

/* vendors */
.vendors h2{position:absolute;top:3040px;left:0;width:1200px;text-align:center;font-size:56px;font-weight:700}
.vendor{position:absolute;top:3212px;width:200px;text-align:center;font-size:22px;font-weight:700;color:#3b3b3b;display:flex;align-items:center;justify-content:center;gap:10px}
.vendor i{width:26px;height:26px;border-radius:50%;background:#6b6b6b;display:block;flex:none}

/* footer */
.footer-rule{top:3326px;left:0;width:1200px;height:5px;background:var(--yellow)}
.footer{top:3331px;left:0;width:1200px;height:171px;background:var(--blue-deep)}
.footer-nav{position:absolute;top:70px;left:145px;display:flex;gap:36px;color:var(--white);font-size:16px}
.copyright{position:absolute;top:116px;left:145px;color:var(--white);font-size:13px;font-weight:300}
.email{position:absolute;top:75px;left:631px;width:251px;height:38px;background:var(--white);font-size:13px;color:var(--text);display:flex;align-items:center;padding-left:16px}
.signup{position:absolute;top:75px;left:882px;width:109px;height:38px;background:var(--yellow);color:var(--blue);font-weight:700;font-size:16px;display:flex;align-items:center;justify-content:center}
.social{position:absolute;top:78px;left:1022px;width:33px;height:33px;border-radius:50%;background:var(--white)}
</style>
</head>
<body>

<div class="abs top-rule"></div>
<header class="abs header"></header>
<div class="abs brand">
  <span class="brand-mark"></span>
  <span class="brand-name">Tidewell<br>Homecare</span>
</div>
<div class="abs phone">
  <svg width="44" height="44" viewBox="0 0 44 44"><circle cx="22" cy="22" r="20" fill="none" stroke="#33a6d7" stroke-width="3"/><path d="M15 13c2-1 3 0 4 3l-2 2c1 3 3 5 6 6l2-2c3 1 4 2 3 4-1 2-3 3-5 2-6-2-10-6-11-12 0-1 1-2 3-3z" fill="#33a6d7"/></svg>
  <span>1 555 014 2290</span>
</div>
<nav class="abs nav">
  <span class="active" style="left:0">HOME</span>
  <span style="left:78px">SERVICES</span>
  <span style="left:180px">GIFT CARDS</span>
  <span style="left:298px">ABOUT</span>
  <span style="left:381px">CONTACT</span>
</nav>
<a class="btn" style="top:60px;left:894px;width:161px;height:38px;font-size:16px">Free Estimate</a>

<section class="abs hero" role="img" aria-label="Bright modern kitchen with wooden cabinets, dining table and blue pendant lamp">
  <h1>The Importance of<br>Good Housekeeping</h1>
  <p>Sed ut perspiciatis unde omnis iste natus error sit<br>voluptatem accusantium doloremque</p>
  <a class="btn" style="top:481px;left:510px;width:178px;height:42px">Free Estimate</a>
  <div class="abs dots"><i></i><i></i><i class="on"></i><i></i><i></i></div>
  <div class="abs arrow" style="top:301px;left:24px"><svg width="14" height="20" viewBox="0 0 14 20"><path d="M10 3L3 10l7 7" fill="none" stroke="#fff" stroke-width="2.5"/></svg></div>
  <div class="abs arrow" style="top:301px;left:1116px"><svg width="14" height="20" viewBox="0 0 14 20"><path d="M4 3l7 7-7 7" fill="none" stroke="#fff" stroke-width="2.5"/></svg></div>
</section>

<div class="abs about-photo" role="img" aria-label="Housekeeper vacuuming the carpet beside a made bed, seen from above"></div>
<section class="abs about">
  <h2>ABOUT US</h2>
  <p>Lorem ipsum dolor sit amet, consectetur adipiscing elit, sed do eiusmod tempor incididunt ut labore et dolore magna aliqua. Quis ipsum suspendisse ultrices gravida. Risus commodo viverra maecenas accumsan lacus vel facilisis. Lorem ipsum dolor sit amet, consectetur adipiscing elit, sed do eiusmod tempor incididunt ut labore et dolore magna aliqua. Quis ipsum suspendisse ultris accumsan lacus vel facilisis.</p>
  <a class="btn" style="top:418px;left:65px;width:186px;height:44px">Get to Know Us</a>
</section>

<section class="abs service" style="left:120px">
  <svg width="84" height="84" viewBox="0 0 84 84" fill="none" stroke="#33a6d7" stroke-width="4"><path d="M4 42L42 6l38 36"/><path d="M14 34v46h56V34"/><rect x="30" y="44" width="24" height="36"/><path d="M42 44v36"/></svg>
  <h3>Residential Cleaning</h3>
  <p>Lorem ipsum dolor sit amet, consectetur adipiscing elit, sed do eiusmod tempor incididunt ut labore et dolore magna aliqua. Quis ipsum suspendisse ultrices gravida. Risus commodo viverra maecenas accumsan lacus vel facilisis.</p>
</section>
<a class="btn" style="top:1744px;left:214px;width:251px;height:45px">Residential Services</a>

<section class="abs service" style="left:639px">
  <svg width="96" height="84" viewBox="0 0 96 84" fill="none" stroke="#33a6d7" stroke-width="3.5"><rect x="22" y="8" width="52" height="70"/><path d="M4 80h88"/><path d="M34 2h28v6"/><g stroke-width="3"><rect x="30" y="18" width="9" height="9"/><rect x="44" y="18" width="9" height="9"/><rect x="58" y="18" width="9" height="9"/><rect x="30" y="34" width="9" height="9"/><rect x="44" y="34" width="9" height="9"/><rect x="58" y="34" width="9" height="9"/><rect x="30" y="50" width="9" height="9"/><rect x="58" y="50" width="9" height="9"/><rect x="42" y="56" width="13" height="22"/></g></svg>
  <h3>Commercial Cleaning</h3>
  <p>Lorem ipsum dolor sit amet, consectetur adipiscing elit, sed do eiusmod tempor incididunt ut labore et dolore magna aliqua. Quis ipsum suspendisse ultrices gravida. Risus commodo viverra maecenas accumsan lacus vel facilisis.</p>
</section>
<a class="btn" style="top:1744px;left:734px;width:251px;height:45px">Commercial Services</a>

<section class="abs estimate">
  <h2>FREE ESTIMATE</h2>
  <div class="field" style="top:194px;left:144px">Name *</div>
  <div class="field" style="top:194px;left:453px">Email *</div>
  <div class="field" style="top:194px;left:761px">City *</div>
  <div class="field" style="top:258px;left:144px">Square Footage *</div>
  <div class="field" style="top:258px;left:453px">Property Type * <svg width="10" height="6"><path d="M0 0h10L5 6z" fill="#222"/></svg></div>
  <div class="field" style="top:258px;left:761px">Type of Cleaning * <svg width="10" height="6"><path d="M0 0h10L5 6z" fill="#222"/></svg></div>
  <div class="field" style="top:322px;left:144px">Frequency&nbsp; * <svg width="10" height="6"><path d="M0 0h10L5 6z" fill="#222"/></svg></div>
  <div class="field" style="top:322px;left:453px">MM / DD / YY * <svg width="13" height="13" viewBox="0 0 13 13"><rect x="0.5" y="1.5" width="12" height="11" fill="none" stroke="#555"/><path d="M0 4.5h13M3 7h2M6 7h2M9 7h2M3 10h2M6 10h2" stroke="#555"/></svg></div>
  <div class="submit" style="top:322px;left:761px">SUBMIT</div>
</section>

<section class="abs testimonial" role="img" aria-label="Cleaning supplies, gloves, brush and spray bottle on a dark wooden surface">
  <svg class="abs" style="top:110px;left:350px" width="90" height="60" viewBox="0 0 90 60"><path d="M4 24a18 18 0 1 1 32 10c-5 9-14 18-24 22l-2-4c6-4 10-9 11-13A18 18 0 0 1 4 24zM50 24a18 18 0 1 1 32 10c-5 9-14 18-24 22l-2-4c6-4 10-9 11-13a18 18 0 0 1-17-15z" fill="#33a6d7"/></svg>
  <p class="quote">Lorem ipsum dolor sit amet, consectetur adipiscing elit, sed do eiusmod tempor incididunt ut labore et dolore magna aliqua. Quis ipsum suspendisse ultrices gravida.</p>
  <p class="author">- Marla</p>
  <svg class="abs" style="top:502px;left:372px" width="44" height="22" viewBox="0 0 44 22"><path d="M10 3L3 11l7 8M34 3l7 8-7 8" fill="none" stroke="#fff" stroke-width="2.5"/></svg>
</section>

<section class="vendors">
  <h2>PREFERRED VENDORS</h2>
  <svg class="abs" style="top:3200px;left:74px" width="34" height="66" viewBox="0 0 34 66"><path d="M32 2L2 33l30 31" fill="none" stroke="#777" stroke-width="1.5"/></svg>
  <div class="vendor" style="left:140px"><i></i>Brightfold Services</div>
  <div class="vendor" style="left:383px">Kestrel &amp; Co</div>
  <div class="vendor" style="left:640px">Pellham Cleaning</div>
  <div class="vendor" style="left:890px"><i></i>Orrin Supply</div>
  <svg class="abs" style="top:3200px;left:1094px" width="34" height="66" viewBox="0 0 34 66"><path d="M2 2l30 31L2 64" fill="none" stroke="#777" stroke-width="1.5"/></svg>
</section>

<div class="abs footer-rule"></div>
<footer class="abs footer">
  <div class="footer-nav"><span>HOME</span><span>SERVICES</span><span>GIFT CARDS</span><span>ABOUT</span><span>CONTACT</span></div>
  <p class="copyright">© Copyright 2020 Tidewell Homecare . All Rights Reserved.</p>
  <div class="email">Enter Email</div>
  <div class="signup">SIGN UP</div>
  <span class="social"></span>
</footer>

</body>
</html>
```